Dultavo.com webside

I want to build a Dultavo.com retail website use on Shopify, reselling three main categories: Office Supplies, Packing Supplies, and Home Consumables. I also wish the webpage has the same functions as the Zelvik home page. The page is split into three different parts with the top being a sliding screen showcasing promotion products, below it being the three categories, and finally, a moving screen showing company missions.
Target Market(s)
U.S online
Industry/Entity Type
Office Supplies, packing Supplies and Home Consumables
Coding
Coded - Design and coding required
Number of Pages Required
5+ page
Look and feel

```html
<!DOCTYPE html>
<html lang="en">
<head>
<meta charset="UTF-8">
<title>Dultavo — Office, Packing &amp; Home Supplies</title>
<link href="https://fonts.googleapis.com/css2?family=Lobster&family=Didact+Gothic&family=Playfair+Display:ital,wght@1,700&family=Poppins:wght@500;700&display=swap" rel="stylesheet">
<style>
:root{
  --green:#1f9a74;
  --green-dark:#17825f;
  --ink:#1c1c1c;
  --text:#3a3a3a;
  --muted:#6b6b6b;
  --light:#f1f1f1;
  --card:#f3f3f3;
  --white:#ffffff;
  --dark:#232323;
}
*{box-sizing:border-box;margin:0;padding:0}
html,body{width:1200px;height:4792px;overflow:hidden}
body{font-family:'Didact Gothic',sans-serif;color:var(--text);background:var(--white);position:relative}
section,header,footer{position:relative;width:1200px;overflow:hidden}
.script{font-family:'Lobster',cursive;font-weight:400;color:var(--ink)}
.btn{display:inline-flex;align-items:center;justify-content:center;border:2px solid var(--green);color:var(--green);border-radius:28px;font-family:'Poppins',sans-serif;font-weight:700;font-size:14px;background:transparent;text-decoration:none}
.body-copy{font-size:12.5px;line-height:26px;color:var(--text)}
.ph{display:block}

/* Hero */
.hero{height:635px}
.hero-bg{position:absolute;inset:0;background:linear-gradient(115deg,#e8e7e3 0%,#dddcd7 45%,#d3cec5 70%,#c9b89e 100%)}
.nav{position:absolute;top:30px;left:112px;right:112px;display:flex;align-items:center;justify-content:space-between}
.logo{font-family:'Lobster',cursive;font-size:30px;color:var(--green)}
.menu{display:flex;gap:34px;align-items:center;font-family:'Lobster',cursive;font-size:16px;color:var(--ink)}
.menu .active{color:var(--green);border-bottom:2px solid var(--green);padding-bottom:2px}
.menu span{display:inline-flex;align-items:center;gap:7px}
.hero-copy{position:absolute;left:112px;top:240px;width:410px}
.hero-copy h1{font-family:'Lobster',cursive;font-size:82px;color:var(--green);font-weight:400;line-height:1}
.hero-copy p{margin-top:22px;font-size:13px;line-height:28px;color:var(--ink)}
.hero-copy .btn{margin-top:28px;width:214px;height:50px}

/* About */
.about{height:513px;background:var(--light);display:flex}
.about-photo{width:600px;height:513px;background:linear-gradient(135deg,#d8c27a,#c99a52 45%,#b07a3e 80%)}
.about-copy{padding:100px 0 0 50px;width:470px}
.about-copy h2{font-size:42px}
.about-copy p{margin-top:20px}
.about-copy .btn{margin-top:26px;width:214px;height:50px}

/* Categories */
.categories{height:623px;text-align:center}
.categories h2{font-size:50px;margin-top:52px}
.cat-grid{display:flex;gap:26px;justify-content:center;margin-top:24px}
.cat{width:310px}
.cat .ph{width:310px;height:274px;background:var(--card);display:flex;align-items:center;justify-content:center}
.cat .ph i{display:block;width:170px;height:140px;border-radius:14px}
.cat h3{font-weight:400;font-size:15px;color:var(--ink);margin-top:18px}
.cat .price{font-size:12px;margin-top:6px}
.categories .btn{margin-top:36px;width:164px;height:48px}

/* Best seller */
.bestseller{height:591px;background:var(--light)}
.bestseller h2{text-align:center;font-size:50px;margin-top:48px}
.prod-grid{position:absolute;left:112px;top:129px;display:flex;gap:14px}
.prod{width:317px}
.prod .ph{width:317px;height:257px}
.prod h3{font-family:'Playfair Display',serif;font-style:italic;font-weight:700;font-size:17px;line-height:26px;color:var(--ink);margin-top:10px}
.prod p{font-size:11.5px;line-height:24px;margin-top:8px}
.prod .price{font-family:'Poppins',sans-serif;font-weight:700;font-size:14px;color:var(--ink);margin-top:24px}
.arrow{position:absolute;top:2030px;width:36px;height:36px}

/* Feature dark */
.feature{height:515px;background:linear-gradient(180deg,#2b2b2b,#1b1b1b);color:var(--white);text-align:center}
.feature h2{font-family:'Lobster',cursive;font-weight:400;font-size:42px;margin-top:136px}
.feature p{width:700px;margin:16px auto 0;font-size:12px;line-height:26px;color:#e8e8e8}
.feature .btn{margin-top:26px;width:216px;height:50px;border-color:var(--white);color:var(--white)}

/* Testimonials */
.testimonials{height:518px;text-align:center}
.testimonials h2{font-size:42px;margin-top:44px}
.t-grid{display:flex;gap:17px;justify-content:center;margin-top:40px}
.t-card{width:232px;height:308px;background:var(--card);padding:20px 22px 0}
.avatar{width:52px;height:52px;border-radius:50%;margin:0 auto;background:linear-gradient(#c9b6a6,#8a7464)}
.t-card h3{font-family:'Playfair Display',serif;font-style:italic;font-weight:700;font-size:13px;color:var(--ink);margin-top:12px}
.t-card p{font-size:11.5px;line-height:21px;margin-top:32px}

/* Offer */
.offer{height:515px;display:flex}
.offer-copy{width:600px;padding:102px 0 0 108px}
.offer-copy h2{font-size:42px}
.offer-copy p{margin-top:16px;width:440px}
.offer-copy .btn{margin-top:26px;width:214px;height:50px}
.offer-photo{width:600px;height:515px;background:linear-gradient(160deg,#e7ece6,#cdd5c8 40%,#b78b5b 75%,#a57a4d)}

/* Newsletter */
.newsletter{height:446px;background:linear-gradient(135deg,#202020,#2f2f2f 50%,#1b1b1b);text-align:center;color:var(--white)}
.newsletter h2{font-family:'Lobster',cursive;font-weight:400;font-size:42px;margin-top:126px}
.newsletter p{font-size:18px;line-height:31px;margin-top:6px}
.signup{display:flex;width:556px;height:68px;margin:28px auto 0;border:2px solid var(--white);border-radius:36px;overflow:hidden}
.signup .field{flex:1;text-align:left;padding:0 26px;line-height:64px;font-size:17px}
.signup .go{width:172px;background:var(--white);color:var(--ink);line-height:64px;font-size:17px;border-radius:34px}

/* Footer */
.site-footer{height:436px;background:var(--green);color:var(--white)}
.f-col{position:absolute;top:60px}
.f-col h4{font-family:'Lobster',cursive;font-weight:400;font-size:26px}
.f-col ul{list-style:none;margin-top:14px}
.f-col li{font-size:12.5px;line-height:35px}
.f-about{left:112px;width:310px}
.f-about p{font-size:11px;line-height:25px;margin-top:12px}
.f-about .contact{margin-top:14px;font-size:12.5px}
.f-about .contact u{text-decoration:underline}
.social li{display:flex;align-items:center;gap:8px}
.social i{display:inline-block;width:11px;height:11px;background:var(--white);border-radius:2px}
.copyright{position:absolute;top:328px;width:100%;text-align:center;font-size:13px}
.pay{position:absolute;top:362px;left:477px;display:flex;gap:10px}
.pay i{display:block;width:40px;height:26px;background:var(--white);border-radius:3px}
</style>
</head>
<body>

<header class="hero">
  <div class="hero-bg" role="img" aria-label="Promotional photo of cardboard shipping boxes on a wooden shelf against a light plaster wall"></div>
  <nav class="nav">
    <div class="logo">Dultavo</div>
    <div class="menu">
      <span class="active">Home</span>
      <span>About Us</span>
      <span>Products</span>
      <span>Blog</span>
      <span>Contact</span>
      <span><svg width="14" height="14" viewBox="0 0 14 14"><circle cx="6" cy="6" r="4.5" fill="none" stroke="#1c1c1c" stroke-width="1.8"/><path d="M9.5 9.5L13 13" stroke="#1c1c1c" stroke-width="1.8"/></svg>Search</span>
      <span><svg width="14" height="15" viewBox="0 0 14 15"><circle cx="7" cy="4.5" r="3.3" fill="none" stroke="#1c1c1c" stroke-width="1.5"/><path d="M1 14c0-3.5 2.7-5.5 6-5.5s6 2 6 5.5" fill="none" stroke="#1c1c1c" stroke-width="1.5"/></svg>Login</span>
      <span><svg width="15" height="15" viewBox="0 0 15 15"><rect x="1" y="5" width="13" height="9" fill="#1c1c1c"/><path d="M4.5 5V3.5a3 3 0 0 1 6 0V5" fill="none" stroke="#1c1c1c" stroke-width="1.5"/></svg>Cart</span>
    </div>
  </nav>
  <div class="hero-copy">
    <h1>Dultavo</h1>
    <p>Lorem ipsum dolor sit amet, consectetur adipiscing elit, sed do eiusmod tempor incididunt ut labore et dolore magna aliqua. Ut enim ad minim veniam, quis nostrud exercitation</p>
    <a class="btn">Buy Now</a>
  </div>
</header>

<section class="about">
  <div class="about-photo ph" role="img" aria-label="Cardboard box filled with pasta, grains, canned goods and cooking oil"></div>
  <div class="about-copy">
    <h2 class="script">About Us</h2>
    <p class="body-copy">Lorem ipsum dolor sit amet, consectetur adipiscing elit, sed do eiusmod tempor incididunt ut labore et dolore magna aliqua. Ut enim ad minim veniam, quis nostrud exercitation ullamco laboris nisi ut aliquip ex ea commodo consequat. Duis aute irure dolor in reprehenderit in voluptate velit esse cillum dolore eu fugiat nulla pariatur. Excepteur sint occaecat cupidatat non proident, sunt in culpa qui officia deserunt mollit anim id est laborum</p>
    <a class="btn">Read More</a>
  </div>
</section>

<section class="categories">
  <h2 class="script">Our Categories</h2>
  <div class="cat-grid">
    <div class="cat">
      <div class="ph" role="img" aria-label="Colored pencils, notebooks and office supplies"><i style="background:linear-gradient(135deg,#f3c53a,#e2463d 50%,#3a8fd8)"></i></div>
      <h3>Office Supplies</h3><div class="price">$ 45.00</div>
    </div>
    <div class="cat">
      <div class="ph" role="img" aria-label="Cardboard box with packing tape roll"><i style="background:linear-gradient(135deg,#caa073,#a87a4c)"></i></div>
      <h3>Packing Supplies</h3><div class="price">$ 45.00</div>
    </div>
    <div class="cat">
      <div class="ph" role="img" aria-label="Folded knitted turquoise blanket"><i style="background:linear-gradient(135deg,#5fc2d1,#3aa1b8 60%,#d36a9a)"></i></div>
      <h3>Home Consumables</h3><div class="price">$ 45.00</div>
    </div>
  </div>
  <a class="btn">See All</a>
</section>

<section class="bestseller">
  <h2 class="script">Best Seller</h2>
  <div class="prod-grid">
    <div class="prod">
      <div class="ph" role="img" aria-label="Spiral notebook with paper clips on a wooden desk" style="background:linear-gradient(135deg,#7a4a2a,#e8e8e8 45%,#6b3f22)"></div>
      <h3>Lorem ipsum dolor sit amet, consectetur adipiscing elit,</h3>
      <p>Lorem ipsum dolor sit amet, consectetur adipiscing elit, sed do eiusmod tempor incididunt ut labore et dolore magna</p>
      <div class="price">$100.00</div>
    </div>
    <div class="prod">
      <div class="ph" role="img" aria-label="Stacked cardboard boxes in a warehouse" style="background:linear-gradient(135deg,#5a3a22,#c68a4e 50%,#8a5a32)"></div>
      <h3>Lorem ipsum dolor sit amet, consectetur adipiscing elit,</h3>
      <p>Lorem ipsum dolor sit amet, consectetur adipiscing elit, sed do eiusmod tempor incididunt ut labore et dolore magna</p>
      <div class="price">$100.00</div>
    </div>
    <div class="prod">
      <div class="ph" role="img" aria-label="Home office desk with computer and shelves" style="background:linear-gradient(160deg,#f2f2f2,#d8d4ce 60%,#9a7a5a)"></div>
      <h3>Lorem ipsum dolor sit amet, consectetur adipiscing elit,</h3>
      <p>Lorem ipsum dolor sit amet, consectetur adipiscing elit, sed do eiusmod tempor incididunt ut labore et dolore magna</p>
      <div class="price">$100.00</div>
    </div>
  </div>
</section>

<svg class="arrow" style="left:55px" viewBox="0 0 36 36"><circle cx="18" cy="18" r="16" fill="#fff" stroke="#1c1c1c" stroke-width="1.5"/><path d="M20.5 12l-6 6 6 6" fill="none" stroke="#1c1c1c" stroke-width="1.8"/></svg>
<svg class="arrow" style="left:1099px" viewBox="0 0 36 36"><circle cx="18" cy="18" r="16" fill="#fff" stroke="#1c1c1c" stroke-width="1.5"/><path d="M15.5 12l6 6-6 6" fill="none" stroke="#1c1c1c" stroke-width="1.8"/></svg>

<section class="feature" role="img" aria-label="Dark photo of a modern office interior behind the text">
  <h2>Office Supplies</h2>
  <p>Lorem ipsum dolor sit amet, consectetur adipiscing elit, sed do eiusmod tempor incididunt ut labore et dolore magna aliqua. Ut enim ad minim veniam, quis nostrud exercitation ullamco laboris nisi ut aliquip ex ea commodo consequat. Duis aute irure dolor in reprehenderit in voluptate velit esse cillum dolore eu fugiat nulla pariatur. Excepteur sint occaecat cupidatat non proident, sunt in culpa qui officia deserunt mollit anim id est laborum</p>
  <a class="btn">Buy Now</a>
</section>

<section class="testimonials">
  <h2 class="script">What Our Customers Says</h2>
  <div class="t-grid">
    <div class="t-card"><div class="avatar" role="img" aria-label="Customer portrait"></div><h3>Patty Orwell.</h3><p>Lorem ipsum dolor sitconsectetur adipiscing elit, sed do eiusmod tempor incididunt ut labore et dolore magna aliqua. Ut enim ad minim veniam, quis nostrud exercitation ullamco laboris nisi ut aliquip ex ea commodo consequat</p></div>
    <div class="t-card"><div class="avatar" role="img" aria-label="Customer portrait"></div><h3>Patty Orwell.</h3><p>Lorem ipsum dolor sitconsectetur adipiscing elit, sed do eiusmod tempor incididunt ut labore et dolore magna aliqua. Ut enim ad minim veniam, quis nostrud exercitation ullamco laboris nisi ut aliquip ex ea commodo consequat</p></div>
    <div class="t-card"><div class="avatar" role="img" aria-label="Customer portrait"></div><h3>Patty Orwell.</h3><p>Lorem ipsum dolor sitconsectetur adipiscing elit, sed do eiusmod tempor incididunt ut labore et dolore magna aliqua. Ut enim ad minim veniam, quis nostrud exercitation ullamco laboris nisi ut aliquip ex ea commodo consequat</p></div>
    <div class="t-card"><div class="avatar" role="img" aria-label="Customer portrait"></div><h3>Patty Orwell.</h3><p>Lorem ipsum dolor sitconsectetur adipiscing elit, sed do eiusmod tempor incididunt ut labore et dolore magna aliqua. Ut enim ad minim veniam, quis nostrud exercitation ullamco laboris nisi ut aliquip ex ea commodo consequat</p></div>
  </div>
</section>

<section class="offer">
  <div class="offer-copy">
    <h2 class="script">Our Offer</h2>
    <p class="body-copy">Lorem ipsum dolor sit amet, consectetur adipiscing elit, sed do eiusmod tempor incididunt ut labore et dolore magna aliqua. Ut enim ad minim veniam, quis nostrud exercitation ullamco laboris nisi ut aliquip ex ea commodo consequat. Duis aute irure dolor in reprehenderit in voluptate velit esse cillum dolore eu fugiat nulla pariatur. Excepteur sint occaecat cupidatat non proident, sunt in culpa qui officia deserunt mollit anim id est laborum</p>
    <a class="btn">Shop Now</a>
  </div>
  <div class="offer-photo ph" role="img" aria-label="Moving boxes stacked in a bright living room beside a green armchair"></div>
</section>

<section class="newsletter" role="img" aria-label="Dark desk with keyboard, pen, glasses and a plant behind the signup form">
  <h2>Stay In The Loop</h2>
  <p>Sign up for our weekly newsletter and receive<br>exclusive coupons and special offers</p>
  <div class="signup"><div class="field">Email</div><div class="go">Signup</div></div>
</section>

<footer class="site-footer">
  <div class="f-col f-about">
    <h4>About Us</h4>
    <p>Lorem ipsum dolor sit amet, consectetur adipiscing elit, sed do eiusmod tempor incididunt ut labore et dolore magna aliqua. Ut enim ad minim veniam, quis nostrud exercitation ullamco laboris nisi ut aliquip ex ea commodo consequat</p>
    <div class="contact">Contact us: <u>dultavo.com</u></div>
  </div>
  <div class="f-col" style="left:690px">
    <h4>Links</h4>
    <ul><li>Home</li><li>About Us</li><li>Products</li><li>Reviews</li><li>Contact</li></ul>
  </div>
  <div class="f-col" style="left:826px">
    <h4>Help</h4>
    <ul><li>Shipping</li><li>Returns</li><li>Payment</li></ul>
  </div>
  <div class="f-col social" style="left:950px">
    <h4>FOLLOW US</h4>
    <ul><li><i></i>Friendwall</li><li><i></i>Snapgrid</li></ul>
  </div>
  <div class="copyright">© 2022 All Rights Reserved</div>
  <div class="pay"><i></i><i></i><i></i><i></i><i></i></div>
</footer>

</body>
</html>
```